Tidewell-Network Theme For Forums!

We are looking for a theme for our forums. The forums are ran off Invision Power Boards. We have a basic theme on there now but we want more our own feel. If possible have some longboarding accept incorporated in the theme. We want the theme to have some red in it to match our logo. Tidewell-network.com

Target Market(s)

Skatingboarding & Longboarding

Coding

Coded - Design and coding required

Number of Pages Required

1 page

Colors
f04a50

```html
<!DOCTYPE html>
<html lang="en">
<head>
<meta charset="utf-8">
<title>Tidewell Network Forums</title>
<link href="https://fonts.googleapis.com/css2?family=Poppins:ital,wght@0,400;0,500;0,600;0,700;1,400&display=swap" rel="stylesheet">
<style>
:root{
  --red:#e30613;
  --black:#000;
  --ink:#1e1e1e;
  --muted:#555;
  --line:#dcdcdc;
  --panel:#fff;
  --page:#f0f0f0;
  --band:#e6e6e6;
  --backdrop:#e1e1ea;
  --dark:#333;
}
*{box-sizing:border-box;margin:0;padding:0}
html,body{width:1149px;height:1200px;overflow:hidden;background:var(--backdrop);font-family:'Poppins',sans-serif;color:var(--ink)}
.stage{width:1436px;height:1500px;transform:scale(.8);transform-origin:0 0;position:relative}
.site{position:absolute;left:155px;top:107px;width:1126px;height:1286px;background:var(--page);border-top:2px solid var(--red);box-shadow:0 10px 40px rgba(60,60,90,.12)}
.abs{position:absolute}
/* header */
.header{position:absolute;left:0;top:0;width:100%;height:69px;background:#fff}
.brand{left:30px;top:24px;display:flex;align-items:center;gap:7px;font-weight:700;font-size:15px;line-height:20px;color:var(--red);letter-spacing:.2px;white-space:nowrap;width:185px;overflow:hidden}
.brand-dot{width:12px;height:12px;background:var(--red);flex:none}
.search{left:228px;top:21px;width:296px;height:29px;border:1px solid #bbb;border-radius:15px;display:flex;align-items:center;font-size:10px;color:#444;overflow:hidden}
.search .q{flex:1;padding-left:13px;font-style:italic}
.search .scope{width:95px;border-left:1px solid #ccc;height:19px;line-height:19px;padding-left:6px;font-style:italic;position:relative}
.search .scope::after{content:"";position:absolute;right:8px;top:8px;border:3px solid transparent;border-top-color:#444}
.search .go{width:31px;height:29px;border-radius:0 15px 15px 0;background:var(--red);display:flex;align-items:center;justify-content:center}
.tool{top:22px}
.badge{position:absolute;top:-4px;right:-8px;width:14px;height:14px;border-radius:50%;background:var(--red);color:#fff;font-size:8px;text-align:center;line-height:14px}
.user{left:974px;top:30px;font-size:11px;color:#333}
.avatar{border-radius:50%;background:radial-gradient(circle at 50% 40%,#d9a88a,#6b4a3a)}
/* nav */
.nav{position:absolute;left:0;top:69px;width:100%;height:47px;background:var(--black);display:flex;padding-left:29px}
.nav a{color:#fff;text-decoration:none;font-size:12px;height:47px;line-height:45px;padding:0 18px;border-right:1px solid #222}
.nav a.on{background:var(--red);padding:0 17px}
.pill0{display:inline-block;width:14px;height:14px;border-radius:50%;background:var(--red);border:1px solid #fff;font-size:8px;line-height:12px;text-align:center;vertical-align:1px}
/* main */
.title{left:28px;top:140px;font-size:18px;font-weight:500}
.newlink{left:960px;top:147px;font-size:13px;font-weight:500;color:var(--red)}
.card{background:var(--panel);border:1px solid var(--line)}
.news{left:29px;top:194px;width:819px;height:44px;font-size:11px;font-weight:500;padding:13px 15px}
.bar{height:36px;background:var(--red);color:#fff;font-size:14px;font-weight:500;padding:9px 14px;position:relative}
.bar .min{position:absolute;right:12px;top:11px;width:14px;height:14px;border-radius:50%;background:#fff;color:var(--red);font-size:12px;line-height:12px;text-align:center}
.topics{left:29px;top:258px;width:819px}
table{border-collapse:collapse;width:100%;background:#fff}
th{font-size:11px;font-weight:600;text-align:left;height:37px;border-bottom:1px solid var(--line);background:#f5f5f5}
td{border-bottom:1px solid var(--line);height:61px;font-size:11px;vertical-align:middle}
.ico{width:56px;border-right:1px solid var(--line);text-align:center}
.thumb{display:inline-block;width:34px;height:34px;border-radius:6px}
.sub{font-size:8px;color:#444;margin-top:5px}
.box{display:inline-block;width:16px;height:16px;border:1px solid #ccc;background:#fafafa}
.ext{display:inline-block;width:9px;height:9px;border:1.5px solid var(--red);margin-left:6px}
.ext.s{width:6px;height:6px;border:1px solid #777;margin-left:3px}
.stats{left:29px;top:654px;width:819px}
.summary{height:37px;background:#f2f2f2;text-align:center;font-size:11px;font-weight:500;line-height:37px;border:1px solid var(--line);border-top:0}
.group{height:35px;background:var(--band);font-size:12px;font-weight:500;line-height:35px;padding-left:15px}
.entry{height:64px;background:#fff;display:flex;align-items:center;padding-left:12px;gap:12px;border-left:1px solid var(--line);border-right:1px solid var(--line);font-size:11px}
.entry .sub a{color:#333;margin-right:12px;text-decoration:underline}
.btns{left:609px;top:1153px;display:flex;gap:3px}
.btn{height:28px;border-radius:14px;color:#fff;font-size:10px;font-weight:500;line-height:28px;padding:0 17px}
.footer{position:absolute;left:0;bottom:0;width:100%;height:55px;background:var(--black);color:#fff;font-size:11px;text-align:center;line-height:52px}
.footer .tag{position:absolute;right:32px;top:8px;font-size:10px}
/* side */
.side{left:885px;width:206px}
.side .bar{height:30px;font-size:12px;padding:6px 10px}
.side .bar .min{top:9px;width:12px;height:12px;font-size:10px;line-height:10px}
.sbody{background:#fff;border:1px solid var(--line);border-top:0}
.mind{margin:5px;height:22px;border:1px solid #ccc;font-size:8px;font-style:italic;line-height:20px;padding-left:8px;position:relative}
.status{display:flex;gap:8px;padding:10px 12px;border-top:1px solid var(--line);height:68px;align-items:center}
.status p{font-size:8px;font-style:italic;line-height:15px}
.status em{color:var(--red)}
.more{text-align:right;font-size:8px;font-weight:500;padding:10px 8px}
.topic{padding:11px 14px 7px;border-bottom:1px solid var(--line);font-size:10px;font-weight:500;height:47px}
.meta{font-size:8px;color:#333;margin-top:5px;font-weight:400}
.tabs{display:flex;gap:25px;align-items:center;padding:13px 8px 8px;font-size:10px}
.tabs .t{background:#333;color:#fff;border-radius:12px;padding:4px 16px}
.watch{padding:8px 10px;border-bottom:1px solid var(--line);font-size:11px;font-weight:500}
.watch span{display:block;font-size:9px;font-weight:400;color:#444;margin-top:3px}
</style>
</head>
<body>
<div class="stage">
<div class="site">
  <header class="header">
    <div class="abs brand"><span class="brand-dot"></span>TIDEWELL NETWORK</div>
    <div class="abs search"><span class="q">Search</span><span class="scope">Forum</span><span class="go"><svg width="10" height="10" viewBox="0 0 10 10"><circle cx="4" cy="4" r="3" stroke="#fff" stroke-width="1.5" fill="none"/><path d="M6 6l3 3" stroke="#fff" stroke-width="1.5"/></svg></span></div>
    <div class="abs tool" style="left:896px;top:28px"><svg width="14" height="11"><rect x=".5" y=".5" width="13" height="10" fill="#555"/><path d="M1 1l6 5 6-5" stroke="#fff" fill="none"/></svg><span class="badge">4</span></div>
    <div class="abs tool" style="left:940px;top:26px"><svg width="13" height="14"><path d="M6.5 1c3 0 4 2 4 5v3l2 2H0l2-2V6c0-3 1-5 4.5-5z" fill="#555"/><circle cx="6.5" cy="13" r="1.5" fill="#555"/></svg><span class="badge">3</span></div>
    <div class="abs user">Marena ▾</div>
    <div class="abs avatar" role="img" aria-label="Member profile photo" style="left:1027px;top:17px;width:37px;height:37px"></div>
    <div class="abs" style="left:1077px;top:30px"><svg width="13" height="11"><ellipse cx="5" cy="4" rx="5" ry="4" fill="#444"/><ellipse cx="9" cy="7" rx="4" ry="3" fill="#444"/></svg></div>
  </header>
  <nav class="nav">
    <a class="on">Forums</a><a>Members</a><a>Calendar</a><a>Blogs</a><a>Gallery</a><a>Files</a><a>Chat <span class="pill0">0</span></a>
    <svg style="position:absolute;right:34px;top:15px" width="17" height="17" viewBox="0 0 17 17"><circle cx="8.5" cy="8.5" r="5.5" fill="none" stroke="#fff" stroke-width="3" stroke-dasharray="3 1.3"/><circle cx="8.5" cy="8.5" r="2" fill="#fff"/></svg>
  </nav>

  <h1 class="abs title">Tidewell Network</h1>
  <div class="abs newlink">View New Content ⟩</div>
  <div class="abs card news">View The Latest News Topic 10</div>

  <section class="abs topics">
    <div class="bar">FORUM TOPICS</div>
    <table>
      <tr><th colspan="2" style="padding-left:15px">TOPIC</th><th>STARTED BY</th><th style="text-align:right;padding-right:43px">STATS</th><th>LAST POST INFO</th><th style="width:45px"><span class="box"></span></th></tr>
      <tr><td class="ico"><span class="thumb" role="img" aria-label="Longboard illustration" style="background:#e9573f;width:16px"></span></td><td style="padding-left:12px">Lorem ipsum dolor sit amectetdo<div class="sub">Lorem ipsum dolor siusmod tem</div></td><td style="width:160px">Kelvoran<span class="ext"></span></td><td style="text-align:right;padding-right:22px;width:140px">10 Replies<div class="sub">111 Views</div></td><td style="width:200px">Today 09:05 Pm<div class="sub">By kelvoran<span class="ext s"></span></div></td><td><span class="box"></span></td></tr>
      <tr><td class="ico"><span class="thumb" role="img" aria-label="Skateboard illustration" style="background:#2d9fd6"></span></td><td style="padding-left:12px">Lorem ipsum dolor sit amectetdo<div class="sub">Lorem ipsum dolor siusmod tem</div></td><td>Kelvoran<span class="ext"></span></td><td style="text-align:right;padding-right:22px">10 Replies<div class="sub">111 Views</div></td><td>Today 09:05 Pm<div class="sub">By kelvoran<span class="ext s"></span></div></td><td><span class="box"></span></td></tr>
      <tr><td class="ico"><span class="thumb" role="img" aria-label="Skateboard illustration" style="background:#f39c32"></span></td><td style="padding-left:12px">Lorem ipsum dolor sit amectetdo<div class="sub">Lorem ipsum dolor siusmod tem</div></td><td>Kelvoran<span class="ext"></span></td><td style="text-align:right;padding-right:22px">10 Replies<div class="sub">111 Views</div></td><td>Today 09:05 Pm<div class="sub">By kelvoran<span class="ext s"></span></div></td><td><span class="box"></span></td></tr>
      <tr><td class="ico"><span class="thumb" role="img" aria-label="Skateboard side view illustration" style="background:#5cc7a8;height:8px"></span></td><td style="padding-left:12px">Lorem ipsum dolor sit amectetdo<div class="sub">Lorem ipsum dolor siusmod tem</div></td><td>Kelvoran<span class="ext"></span></td><td style="text-align:right;padding-right:22px">10 Replies<div class="sub">111 Views</div></td><td>Today 09:05 Pm<div class="sub">By kelvoran<span class="ext s"></span></div></td><td><span class="box"></span></td></tr>
      <tr><td class="ico" style="height:56px"><span class="thumb" role="img" aria-label="Skateboard illustration" style="background:#4fd3e0"></span></td><td style="padding-left:12px">Lorem ipsum dolor sit amectetdo<div class="sub">Lorem ipsum dolor siusmod tem</div></td><td>Kelvoran<span class="ext"></span></td><td style="text-align:right;padding-right:22px">10 Replies<div class="sub">111 Views</div></td><td>Today 09:05 Pm<div class="sub">By kelvoran<span class="ext s"></span></div></td><td><span class="box"></span></td></tr>
    </table>
  </section>

  <section class="abs stats">
    <div class="bar">BOARD STATISTICS<span class="min">–</span></div>
    <div class="summary">Today's Active Topics. The Moderating team. Today's 10 posters .</div>
    <div class="group">Lorem ipsum dolor sit amectetdo</div>
    <div class="entry"><span class="thumb" role="img" aria-label="Skateboard illustration" style="background:#f58a3a"></span><div>Lorem ipsum dolor sit amet, consectetur adipiscing elit, sed do eiusm<div class="sub">Show Detailed by: <a>Last Click</a><a>Member Name</a></div></div></div>
    <div class="group">Lorem ipsum dolor sit amectetdo</div>
    <div class="entry"><span class="thumb" role="img" aria-label="Skateboard illustration" style="background:#5b6f80"></span><div>Lorem ipsum dolor sit amet, consectetur adipiscing elit, sed do eiusm<div class="sub">Show Detailed by: <a>Last Click</a><a>Member Name</a></div></div></div>
    <div class="group">Lorem ipsum dolor sit amectetdo</div>
    <div class="entry"><span class="thumb" role="img" aria-label="Skateboard illustration" style="background:#6cc04a"></span><div>Lorem ipsum dolor sit amet, consectetur adipiscing elit, sed do eiusm<div class="sub">Show Detailed by: <a>Last Click</a><a>Member Name</a></div></div></div>
    <div class="group">Lorem ipsum dolor sit amectetdo</div>
    <div class="entry" style="border-bottom:1px solid var(--line);height:63px"><span class="thumb" role="img" aria-label="Skateboard illustration" style="background:#1f6f7a;height:18px"></span><div>Lorem ipsum dolor sit amet, consectetur adipiscing elit, sed do eiusm<div class="sub">Show Detailed by: <a>Last Click</a><a>Member Name</a></div></div></div>
  </section>

  <div class="abs btns"><span class="btn" style="background:var(--red)">WATCH FORUM</span><span class="btn" style="background:var(--dark)">START NEW TOPIC</span></div>

  <aside class="abs side" style="top:194px">
    <div class="bar">Recent Status Updates<span class="min">–</span></div>
    <div class="sbody">
      <div class="mind">Whats on your mind<span style="position:absolute;right:8px;font-style:normal">⟶</span></div>
      <div class="status"><span class="avatar" role="img" aria-label="Member photo" style="width:45px;height:45px;flex:none"></span><p>Sed ut perspiciatis unde omnis iste natus error sit volupt.<br><em>June 02 2018</em>&nbsp;&nbsp; Comments</p></div>
      <div class="status"><span class="avatar" role="img" aria-label="Member photo" style="width:45px;height:45px;flex:none"></span><p>Sed ut perspiciatis unde omnis iste natus error sit volupt.<br><em>June 02 2018</em>&nbsp;&nbsp; Comments</p></div>
      <div class="status"><span class="avatar" role="img" aria-label="Member photo" style="width:45px;height:45px;flex:none"></span><p>Sed ut perspiciatis unde omnis iste natus error sit volupt.<br><em>June 02 2018</em>&nbsp;&nbsp; Comments</p></div>
      <div class="status"><span class="avatar" role="img" aria-label="Member photo" style="width:45px;height:45px;flex:none"></span><p>Sed ut perspiciatis unde omnis iste natus error sit volupt.<br><em>June 02 2018</em>&nbsp;&nbsp; Comments</p></div>
      <div class="status"><span class="avatar" role="img" aria-label="Member photo" style="width:45px;height:45px;flex:none"></span><p>Sed ut perspiciatis unde omnis iste natus error sit volupt.<br><em>June 02 2018</em>&nbsp;&nbsp; Comments</p></div>
      <div class="more" style="border-top:1px solid var(--line)">View All Updates</div>
    </div>
  </aside>

  <aside class="abs side" style="top:659px">
    <div class="bar">Recently Added Topics<span class="min">–</span></div>
    <div class="sbody">
      <div class="topic">Finibus Bonorum et Malorum<div class="meta">◷ 15:48 &nbsp;&nbsp;&nbsp;&nbsp; ● 158</div></div>
      <div class="topic">Finibus Bonorum et Malorum<div class="meta">◷ 15:48 &nbsp;&nbsp;&nbsp;&nbsp; ● 158</div></div>
      <div class="topic">Finibus Bonorum et Malorum<div class="meta">◷ 15:48 &nbsp;&nbsp;&nbsp;&nbsp; ● 158</div></div>
      <div class="topic">Finibus Bonorum et Malorum<div class="meta">◷ 15:48 &nbsp;&nbsp;&nbsp;&nbsp; ● 158</div></div>
      <div class="topic" style="border-bottom:0">Finibus Bonorum et Malorum<div class="meta">◷ 15:48 &nbsp;&nbsp;&nbsp;&nbsp; ● 158</div></div>
    </div>
  </aside>

  <aside class="abs side" style="top:939px">
    <div class="bar">Watched Content<span class="min">–</span></div>
    <div class="sbody">
      <div class="tabs"><span class="t">Forums</span><span>Topics</span></div>
      <div class="watch">Consequuntur<span>Sed ut perspiciatis unde omni.</span></div>
      <div class="watch" style="border-bottom:0;padding-bottom:14px">Consequuntur<span>Sed ut perspiciatis unde omni.</span></div>
    </div>
  </aside>

  <footer class="footer">Copyrights @ 2018. All Rights Reserved.<span class="tag">C4</span></footer>
</div>
</div>
</body>
</html>
```